Bork Ventures, Inc. Website redesign

Revamp the website, it is old and outdated. www.borkventuresinc.example

Target Market(s)

Information Technology Consulting and Staffing

Coding

Coded - Design and coding required

Number of Pages Required

5+ page

Colors

Designer to choose colors to be used in the design.

Requirements
Must have
• Outlined text boxes just like from the Tolvane.example site. A clean look

```html
<!DOCTYPE html>
<html lang="en">
<head>
<meta charset="utf-8">
<title>Bork Ventures, Inc.</title>
<link rel="stylesheet" href="https://fonts.googleapis.com/css2?family=Montserrat:wght@500;600;700;800&family=Open+Sans:wght@400;600&display=swap">
<style>
:root{
  --crimson:#9d1b32;
  --ink:#333;
  --text:#555;
  --muted:#888;
  --soft:#f4f4f4;
  --footer:#333333;
  --white:#fff;
}
*{box-sizing:border-box;margin:0;padding:0}
html,body{width:1200px;height:3339px;overflow:hidden}
body{position:relative;background:var(--white);font-family:"Open Sans",Arial,sans-serif;color:var(--text)}
.heading{font-family:"Montserrat",Arial,sans-serif}
.btn{display:flex;align-items:center;justify-content:center;background:var(--crimson);color:var(--white);font-family:"Montserrat",Arial,sans-serif;font-weight:600;text-decoration:none;position:absolute}

/* header */
.site-header{position:absolute;top:0;left:0;width:1200px;height:101px;border-bottom:1px solid #e4e4e4;background:var(--white)}
.brand{position:absolute;left:112px;top:28px;display:flex;align-items:center;gap:12px}
.brand-name{font-family:"Montserrat",Arial,sans-serif;font-weight:800;font-size:30px;color:#222;letter-spacing:1px}
.brand-mark{width:22px;height:22px;background:var(--crimson)}
.main-nav{position:absolute;left:456px;top:40px;display:flex;gap:44px;font-family:"Montserrat",Arial,sans-serif;font-size:14.5px;font-weight:500;color:#333}
.main-nav a{color:inherit;text-decoration:none;position:relative}
.main-nav a.active{color:var(--crimson)}
.main-nav a.active::after{content:"";position:absolute;left:0;right:0;top:25px;height:3px;background:var(--crimson)}

/* hero */
.hero{position:absolute;top:101px;left:0;width:1200px;height:619px;background:linear-gradient(180deg,#5d6066 0%,#3c3f44 55%,#2a2c30 100%);text-align:center;color:var(--white)}
.hero-title{position:absolute;top:185px;width:100%;font-size:86px;font-weight:800;letter-spacing:1px;line-height:1}
.hero-sub{position:absolute;top:290px;width:100%;font-size:24px;letter-spacing:.3px}
.hero .btn{left:516px;top:354px;width:169px;height:54px;font-size:16px}
.dots{position:absolute;top:566px;left:568px;display:flex;gap:14px}
.dots span{width:12px;height:12px;border-radius:50%;background:var(--white);border:2px solid var(--white)}
.dots span.current{background:transparent}

/* welcome */
.welcome{position:absolute;top:720px;left:0;width:1200px;height:537px}
.welcome-photo{position:absolute;left:122px;top:90px;width:408px;height:372px;background:linear-gradient(160deg,#aab3c2 0%,#6f8fc8 50%,#2f5fb8 100%)}
.welcome-title{position:absolute;left:610px;top:106px;font-size:32px;font-weight:700;color:var(--crimson);letter-spacing:.5px}
.welcome-copy{position:absolute;left:614px;top:158px;width:480px;font-size:14px;line-height:23px;color:#444}
.welcome-copy p+p{margin-top:5px}
.welcome .btn{left:616px;top:356px;width:155px;height:50px;font-size:16px}

/* about */
.about{position:absolute;top:1257px;left:0;width:1200px;height:510px;background:linear-gradient(180deg,#c07486 0%,#a9546b 55%,#8e3a55 100%);text-align:center;color:var(--white)}
.about-title{margin-top:82px;font-size:37px;font-weight:700}
.about-copy{width:880px;margin:22px auto 0;font-size:16.5px;line-height:28.5px}
.about-copy p+p{margin-top:20px}
.btn-outline{position:absolute;left:507px;top:351px;width:186px;height:60px;border:2px solid var(--white);display:flex;align-items:center;justify-content:center;font-family:"Montserrat",Arial,sans-serif;font-weight:600;font-size:19px;color:var(--white)}

/* services */
.services{position:absolute;top:1767px;left:0;width:1200px;height:705px;background:var(--soft);text-align:center}
.services-title{margin-top:62px;font-size:34px;font-weight:700;color:var(--crimson)}
.services-intro{width:920px;margin:20px auto 0;font-size:12.5px;line-height:23px;color:#444}
.service{position:absolute;top:208px;width:230px;text-align:center}
.service svg{display:block;margin:0 auto}
.service-name{margin-top:10px;font-family:"Montserrat",Arial,sans-serif;font-size:16.5px;font-weight:600;color:#333}
.service-text{margin-top:10px;padding:0 6px;font-size:12.5px;line-height:23px;color:#555}
.service .btn{position:absolute;left:51px;top:360px;width:127px;height:44px;font-size:13.5px;font-weight:500}

/* news */
.news{position:absolute;top:2472px;left:0;width:1200px;height:543px;text-align:center}
.news-title{margin-top:72px;font-size:25px;font-weight:600;color:#444;letter-spacing:.5px}
.news-sub{margin-top:12px;font-size:16px;color:var(--muted)}
.news-card{position:absolute;top:180px;width:308px;text-align:left}
.news-thumb{width:308px;height:156px}
.news-card h3{margin:30px 0 0 4px;font-family:"Montserrat",Arial,sans-serif;font-size:17px;font-weight:500;color:#333}
.news-card p{margin:8px 0 0 4px;font-size:12px;line-height:20.5px;color:#444}
.news-card time{display:block;margin:14px 0 0 6px;font-size:10.5px;color:#444}

/* footer */
.site-footer{position:absolute;top:3015px;left:0;width:1200px;height:324px;background:var(--footer);color:var(--white)}
.footer-col{position:absolute;top:60px}
.footer-col h4{font-family:"Montserrat",Arial,sans-serif;font-size:18px;font-weight:700;letter-spacing:.4px;line-height:22px}
.footer-list{list-style:none;margin-top:28px;font-size:13.5px}
.footer-list.no-head{margin-top:50px}
.footer-list li{height:30px}
.footer-list svg{vertical-align:-2px;margin-right:6px}
.addr{line-height:16px;height:auto !important;margin-bottom:20px;display:flex}
.footer-rule{position:absolute;left:112px;right:112px;top:256px;border-top:1px solid #4a4a4a}
.copyright{position:absolute;left:112px;top:279px;font-size:13px}
.legal{position:absolute;left:893px;top:281px;font-size:10.5px;color:#8a8a8a}
.page-code{position:absolute;left:1139px;top:280px;font-size:12.5px}
</style>
</head>
<body>

<header class="site-header">
  <div class="brand"><span class="brand-name">BORK VENTURES</span><span class="brand-mark"></span></div>
  <nav class="main-nav">
    <a class="active" href="#">HOME</a><a href="#">ABOUT US</a><a href="#">SERVICES</a><a href="#">STRATEGY</a><a href="#">IT NEWS</a><a href="#">CONTACT US</a>
  </nav>
</header>

<section class="hero" role="img" aria-label="Photo of a modern open-plan office with pendant lamps and a city skyline through large windows">
  <h1 class="hero-title heading">BORK VENTURES</h1>
  <p class="hero-sub">Bringing Thought Leadership and Quality to Every Project</p>
  <a class="btn" href="#">LEARN MORE</a>
  <div class="dots"><span class="current"></span><span></span><span></span></div>
</section>

<section class="welcome">
  <div class="welcome-photo" role="img" aria-label="Photo of network server racks and blue patch cables"></div>
  <h2 class="welcome-title heading">WELCOME TO BORK VENTURES</h2>
  <div class="welcome-copy">
    <p>Bork Ventures, Inc. is an 8(a) full-service IT consulting company based in the Washington, DC Metro area. We offer specialized, highly customized technology solutions for our customers located throughout the United States.</p>
    <p>No two businesses are the same. We believe the technology supporting your business operations should align with your company. Every project begins with a thorough analysis of your current technology environment.</p>
  </div>
  <a class="btn" href="#">LEARN MORE</a>
</section>

<section class="about" role="img" aria-label="Aerial city view at dusk with a connected-network overlay, tinted crimson">
  <h2 class="about-title heading">ABOUT US</h2>
  <div class="about-copy">
    <p>Bork Ventures, Inc. is an 8(a) innovative and rapidly growing full-service IT consulting firm. We provide our clients with cutting-edge technologies and the know-how to apply them to their individual business models.</p>
    <p>For over 20 + years, we have been providing reliable IT solutions to businesses in the Washington, DC area and beyond. Our comprehensive services provide clients with unique technology solutions that are customized to meet the specific demands of their business.</p>
  </div>
  <span class="btn-outline">LEARN MORE</span>
</section>

<section class="services">
  <h2 class="services-title heading">BORK VENTURES SERVICES</h2>
  <p class="services-intro">Bork Ventures, Inc. organizes our Services into four key areas. While these four services can be implemented individually the majority of our projects successfuly combine componets from each. Our people and our process is what makes us successful in providing these services.</p>

  <div class="service" style="left:103px">
    <svg width="158" height="182" viewBox="0 0 158 182"><polygon points="79,0 158,45 158,137 79,182 0,137 0,45" fill="var(--crimson)"/>
      <g fill="none" stroke="#fff" stroke-width="2.5"><rect x="59" y="71" width="40" height="40"/><rect x="70" y="82" width="18" height="18"/>
      <path d="M65 63v8M73 63v8M81 63v8M89 63v8M65 111v8M73 111v8M81 111v8M89 111v8M51 77h8M51 85h8M51 93h8M51 101h8M99 77h8M99 85h8M99 93h8M99 101h8"/></g></svg>
    <div class="service-name">Hardware / Software Sales</div>
    <p class="service-text">We have access to multiple distributor partners throughout North America, as well as Elite Partner Status with many of the industry's marquee manufacturers</p>
    <a class="btn" href="#">LEARN MORE</a>
  </div>

  <div class="service" style="left:357px">
    <svg width="158" height="182" viewBox="0 0 158 182"><polygon points="79,0 158,45 158,137 79,182 0,137 0,45" fill="var(--crimson)"/>
      <g fill="none" stroke="#fff" stroke-width="2.5" stroke-linejoin="round"><path d="M38 78l14-14 16 10 10-4 12 4 16-10 14 14-14 16"/><path d="M52 86l20 20c4 4 10 4 12 0l18-18"/><path d="M64 96l10 10M72 88l12 12"/></g></svg>
    <div class="service-name">Professional Services</div>
    <p class="service-text">Our team provides experienced lead-ership and guidance, utilizing the industry standard methodologies. We help you maintain a comprehensive view of strategy.</p>
    <a class="btn" href="#">LEARN MORE</a>
  </div>

  <div class="service" style="left:612px">
    <svg width="158" height="182" viewBox="0 0 158 182"><polygon points="79,0 158,45 158,137 79,182 0,137 0,45" fill="var(--crimson)"/>
      <g fill="none" stroke="#fff" stroke-width="2.5"><rect x="44" y="72" width="34" height="24"/><path d="M38 102h46"/><circle cx="84" cy="82" r="14"/><path d="M94 92l22 16"/></g></svg>
    <div class="service-name">Technology Assessment</div>
    <p class="service-text">Experience has shown companies that perform objective, third-party technol-ogy assessments have proven to be instrumental in identifying weak-nesses or breaches.</p>
    <a class="btn" href="#">LEARN MORE</a>
  </div>

  <div class="service" style="left:866px">
    <svg width="158" height="182" viewBox="0 0 158 182"><polygon points="79,0 158,45 158,137 79,182 0,137 0,45" fill="var(--crimson)"/>
      <g fill="none" stroke="#fff" stroke-width="2.5" stroke-linecap="round"><circle cx="68" cy="76" r="9"/><path d="M65 88h6M68 58v-5M54 64l-4-4M82 64l4-4M50 76h-5"/><path d="M76 70c18-6 34 6 30 24-1 5 4 8 2 12h-8v10H84"/></g></svg>
    <div class="service-name">Technology Consulting</div>
    <p class="service-text">Implementing quality solutions is more than applying technology to problems. You need experts with deep technical knowledge and broad industry experience</p>
    <a class="btn" href="#">LEARN MORE</a>
  </div>
</section>

<section class="news">
  <h2 class="news-title heading">LATEST NEWS</h2>
  <p class="news-sub">At vero eos et accusamus et iusto odio dignissimos ducimus</p>
  <article class="news-card" style="left:112px">
    <div class="news-thumb" role="img" aria-label="Photo of a technician with a laptop in a server room" style="background:linear-gradient(90deg,#d9dde2,#59606a)"></div>
    <h3>Numquam Eius Modi Tempora</h3>
    <p>Class aptent taciti sociosqu ad litora torquent per co nubia nostra per inceptos hymenaeos</p>
    <time>12 JAN 2018</time>
  </article>
  <article class="news-card" style="left:446px">
    <div class="news-thumb" role="img" aria-label="Photo of hands typing with a digital security lock overlay" style="background:linear-gradient(135deg,#0d2e5a,#2a67a6)"></div>
    <h3>Accusantium Doloremque Lauda</h3>
    <p>Class aptent taciti sociosqu ad litora torquent per co nubia nostra per inceptos hymenaeos</p>
    <time>25 FEB 2018</time>
  </article>
  <article class="news-card" style="left:780px">
    <div class="news-thumb" role="img" aria-label="Photo of business team silhouettes against a digital globe" style="background:linear-gradient(180deg,#9fb0cc,#1c2a48)"></div>
    <h3>Quia Consequuntur Magni Dolore</h3>
    <p>Class aptent taciti sociosqu ad litora torquent per co nubia nostra per inceptos hymenaeos</p>
    <time>12 MAR 2018</time>
  </article>
</section>

<footer class="site-footer">
  <div class="footer-col" style="left:112px">
    <h4>QUICK LINKS</h4>
    <ul class="footer-list"><li>Home</li><li>About us</li><li>Services</li><li>Strategy</li></ul>
  </div>
  <div class="footer-col" style="left:343px">
    <ul class="footer-list no-head"><li>News</li><li>Contact</li><li>Site Map</li></ul>
  </div>
  <div class="footer-col" style="left:557px">
    <h4>CONTACT US</h4>
    <ul class="footer-list">
      <li class="addr"><svg width="10" height="13" viewBox="0 0 10 13"><path d="M5 0a5 5 0 0 1 5 5c0 3-5 8-5 8S0 8 0 5a5 5 0 0 1 5-5z" fill="#fff"/><circle cx="5" cy="5" r="2" fill="var(--footer)"/></svg><span>Bork Ventures, Inc. 220 Alder Crest Rd<br>Fenwick, MD 20990</span></li>
      <li style="height:37px"><svg width="12" height="12" viewBox="0 0 12 12"><path d="M2 0l3 3-1.5 2a7 7 0 0 0 3.5 3.5L9 7l3 3-2 2C5 12 0 7 0 2z" fill="#fff"/></svg>301-555-0142</li>
      <li><svg width="13" height="10" viewBox="0 0 13 10"><rect width="13" height="10" fill="#fff"/><path d="M0 0l6.5 5L13 0" fill="none" stroke="var(--footer)" stroke-width="1.3"/></svg>info@borkventures.example</li>
    </ul>
  </div>
  <div class="footer-col" style="left:902px">
    <h4>CONNECT WITH US</h4>
    <ul class="footer-list">
      <li><svg width="10" height="10"><circle cx="5" cy="5" r="5" fill="#fff"/></svg>Friendsbook</li>
      <li><svg width="10" height="10"><circle cx="5" cy="5" r="5" fill="#fff"/></svg>Chirper</li>
      <li><svg width="10" height="10"><circle cx="5" cy="5" r="5" fill="#fff"/></svg>Snapgram</li>
      <li><svg width="10" height="10"><circle cx="5" cy="5" r="5" fill="#fff"/></svg>Viewtube</li>
    </ul>
  </div>
  <div class="footer-rule"></div>
  <p class="copyright">Copyrights © 2019  Bork Ventures. All rights reserved.</p>
  <p class="legal">Terms and Conditions | Privacy Policy</p>
  <p class="page-code">C16</p>
</footer>

</body>
</html>
```